WP website design for Kemble

We need a wordpress design that will incorporate a professional color scheme with company logo in a clean layout. The design needs to consider that this will be developed on a responsive theme. Colors are will be the green of the logo and any others that will creatively highlight it.

Industry/Entity Type

It Company

Font styles to use
Sans Serif

Requirements
Must have
• Navigation: 1) Home 2) Auctions 3) Auction Services 4) Sellers 5) TR Kemble Livestock 6) About Us 7) Contact Us
Site will have slideshow element, image attached.
Widgets will be: 1)Email Signup form 2) Featured Auctions widget 3) Social Media (FB, Youtube, RSS) 4) News & Events blog
Footer will have smaller company logo, association logos (attached) and contact info (below)
▪ T.R. Kemble Inc. / Auctioneers
▪ 4710 NC Hwy 91
▪ Warrenton, NC 27589
▪ Office: (555) 318-6402
▪ Cell: (555) 274-8813
▪ email: trkemble@trkemble-example.com
Nice to have
• Site will have drop-down menus - please indicate the styling, for instance the dropdown menus

```html
<!DOCTYPE html>
<html lang="en">
<head>
<meta charset="utf-8">
<title>T.R. Kemble Inc. / Auctioneers</title>
<link rel="stylesheet" href="https://fonts.googleapis.com/css2?family=Mulish:wght@400;600;700&display=swap">
<style>
:root{
  --green:#3e9a1c;
  --green-dark:#2d7a12;
  --orange:#f29a2e;
  --orange-light:#f7b04a;
  --ink:#1c1c1c;
  --text:#666;
  --muted:#9a9a9a;
  --line:#dcdcdc;
  --band:#efefef;
  --footer:#f6f6f6;
  --icon:#8a8a8a;
}
*{box-sizing:border-box;margin:0;padding:0}
html,body{width:723px;height:1200px;overflow:hidden}
body{position:relative;background:#fff;font-family:"Mulish",sans-serif;color:var(--text)}
.abs{position:absolute}

/* header */
.brand{left:80px;top:12px;display:flex;align-items:center;gap:8px}
.brand-dot{width:26px;height:26px;border-radius:50%;background:var(--green)}
.brand-name{color:var(--green);font-weight:700;font-size:17px;line-height:1.1}
.brand-name small{display:block;font-size:11px;font-weight:600}
.contact-now{right:78px;top:34px;text-align:right;font-size:10.5px;color:#555}
.contact-row{display:flex;align-items:flex-end;justify-content:flex-end;gap:16px;margin-top:2px}
.social{display:flex;gap:3px;margin-bottom:2px}
.social span{width:12px;height:12px;background:var(--icon);border-radius:2px}
.phone{color:var(--green);font-size:16px;font-weight:600;line-height:1.1}

/* nav */
.nav{left:0;top:77px;width:723px;height:31px;background:linear-gradient(#57b02a,var(--green-dark));display:flex;padding-left:74px}
.nav a{color:#fff;text-decoration:none;font-size:10px;font-weight:700;line-height:31px;padding:0 12px;border-right:1px solid rgba(255,255,255,.25)}
.nav a:last-child{border-right:0}

/* slider */
.band{left:0;top:108px;width:723px;height:204px;background:var(--band)}
.slide{left:66px;top:117px;width:591px;height:263px;background:linear-gradient(#c9dbe8 0%,#b89a68 40%,#c9a24c 55%,#8a6e3e 75%,#cbb48a 100%);box-shadow:0 2px 6px rgba(0,0,0,.25)}
.caption{left:66px;top:210px;width:283px;height:86px;background:var(--orange);clip-path:polygon(0 0,100% 0,88% 100%,0 100%);padding:11px 20px;color:#fff}
.caption h2{font-size:15.5px;font-weight:600;white-space:nowrap;line-height:1.2}
.caption h3{font-size:10.5px;font-weight:400;margin-top:2px;white-space:nowrap}
.caption p{font-size:7.5px;opacity:.85;margin-top:4px;line-height:1.55;width:215px}
.pager{left:328px;top:358px;width:76px;height:22px;background:#555;border-radius:16px 16px 0 0;display:flex;justify-content:center;align-items:center;gap:3px}
.pager i{width:7px;height:7px;border-radius:50%;background:#fff}

/* auctions */
.section-title{left:68px;top:411px;font-size:15px;color:var(--ink);font-weight:600}
.auction{left:67px;width:405px;height:118px;display:flex;gap:10px}
.auction .photo{width:136px;height:116px;flex:none;border:1px solid var(--line);border-radius:3px}
.house{background:linear-gradient(#6b9edb,#c7ccd2 45%,#e6e6e6 80%,#7a9a5a)}
.tool{background:radial-gradient(circle,#9aa 0%,#fff 60%)}
.robot{background:radial-gradient(circle,#f0902a 0%,#fff 60%)}
.auction h4{color:var(--green);font-size:11px;font-weight:600;margin-top:3px}
.auction h5{color:var(--ink);font-size:9px;font-weight:400;margin:2px 0 5px}
.auction p{font-size:7px;line-height:12.3px}

/* sidebar */
.widget{left:487px;width:167px;border:1px solid var(--line);border-radius:3px;overflow:hidden}
.widget-head{background:#f3f3f3;border-bottom:1px solid var(--line);padding:10px 15px;font-size:13px;color:var(--ink)}
.feat{display:flex;gap:6px;padding:0 12px 0 16px;margin-top:14px}
.feat .thumb{width:52px;height:40px;flex:none;background:linear-gradient(#6b9edb,#e4e4e4 55%,#7a8a5a)}
.feat-title{display:block;color:var(--green);font-size:7px}
.feat-date{font-size:6.5px;color:#555;display:block;margin:3px 0}
.feat-text{font-size:6px;line-height:1.4;display:block;color:var(--muted)}
.news-title{font-size:13px;color:var(--ink);padding:13px 15px 0}
.news-sub{font-size:6.5px;color:#bbb;padding:3px 15px 0}
.field{margin:6px 15px 0;height:20px;border:1px solid var(--line);background:#f7f7f7;font-size:6.5px;line-height:19px;padding-left:8px;color:#666}
.btn{margin:6px 15px 0;width:68px;height:19px;background:var(--green);color:#fff;font-size:8px;font-weight:700;text-align:center;line-height:19px}
.blog-head{background:linear-gradient(var(--orange-light),var(--orange));color:#fff;padding:8px 15px;font-size:13px}
.post{padding:0 15px;margin-top:11px}
.post-title{display:block;font-size:8.5px;color:#333}
.post-text{display:block;font-size:6.3px;color:var(--muted);line-height:1.6;margin-top:3px}

/* footer */
.footer{left:0;top:1018px;width:723px;height:147px;background:var(--footer);border-top:1px solid var(--line)}
.footer-contact{left:72px;top:1042px;font-size:8px;color:#333;line-height:14px}
.footer-contact h6{font-size:12px;font-weight:400;margin-bottom:3px}
.footer-brand{left:285px;top:1078px;display:flex;align-items:center;gap:8px}
.badges{left:471px;top:1060px;display:flex;gap:12px;align-items:center}
.badges span{background:#c9c9c9}
.copyright{left:0;top:1165px;width:723px;height:35px;background:#fff;border-top:1px solid var(--line);font-size:7px;color:#555;padding:12px 0 0 75px}
</style>
</head>
<body>

<header>
  <div class="abs brand"><span class="brand-dot"></span><div class="brand-name">T.R. Kemble<small>Inc. / Auctioneers</small></div></div>
  <div class="abs contact-now">Contact Us Now
    <div class="contact-row">
      <div class="social" aria-label="Social media links"><span></span><span></span><span></span></div>
      <span class="phone">(555) 610-2290</span>
    </div>
  </div>
</header>

<nav class="abs nav">
  <a href="#">HOME</a><a href="#">AUCTIONS</a><a href="#">AUCTION SERVICES</a><a href="#">SELLERS</a><a href="#">TR KEMBLE LIVESTOCK</a><a href="#">ABOUT US</a><a href="#">CONTACT US</a>
</nav>

<div class="abs band"></div>
<div class="abs slide" role="img" aria-label="Autumn pond with bare trees reflected in the water"></div>
<div class="abs caption">
  <h2>VIVAMUS PORTTITOR PURUS</h2>
  <h3>CUM SOCIIS NATOQUE PENATIBUS</h3>
  <p>Morbi ornare gravida elit Integer congue augue et malesu ada iaculis ipsum dui aliquet felis at cursus magna</p>
</div>
<div class="abs pager"><i></i><i></i><i></i><i></i></div>

<h1 class="abs section-title">UPCOMING AUCTIONS</h1>

<article class="abs auction" style="top:441px">
  <div class="photo house" role="img" aria-label="Two-storey house with porch"></div>
  <div><h4>SUSPENDISSE QUAM LEO MOLESTIE</h4><h5>Morbi porta libero ullamcorper</h5>
  <p>Maple Ridge Country Club, 1840 Birch Ln., Fairview, KY 40299<br>The 22nd annual Golf Tournament and Celebrity Cocktail Party/Auction is a major fundraiser for the many programs offered by the RCL. The golf tournament will be followed as always by a scrumptious dinner, cocktails, and a silent and live auction.<br>If you would like more information please call (555) 406-1187.</p></div>
</article>
<article class="abs auction" style="top:579px">
  <div class="photo house" role="img" aria-label="Yellow house with white porch"></div>
  <div><h4>CURABITUR VEL MI SIT AMET MAGNA</h4><h5>Morbi porta libero ullamcorper</h5>
  <p>Maple Ridge Country Club, 1840 Birch Ln., Fairview, KY 40299<br>The 22nd annual Golf Tournament and Celebrity Cocktail Party/Auction is a major fundraiser for the many programs offered by the RCL. The golf tournament will be followed as always by a scrumptious dinner, cocktails, and a silent and live auction.<br>If you would like more information please call (555) 406-1187.</p></div>
</article>
<article class="abs auction" style="top:720px">
  <div class="photo tool" role="img" aria-label="Power tools"></div>
  <div><h4>DICTUM EGET FERMENTUM</h4><h5>Morbi porta libero ullamcorper</h5>
  <p>Maple Ridge Country Club, 1840 Birch Ln., Fairview, KY 40299<br>The 22nd annual Golf Tournament and Celebrity Cocktail Party/Auction is a major fundraiser for the many programs offered by the RCL. The golf tournament will be followed as always by a scrumptious dinner, cocktails, and a silent and live auction.<br>If you would like more information please call (555) 406-1187.</p></div>
</article>
<article class="abs auction" style="top:858px">
  <div class="photo robot" role="img" aria-label="Orange industrial robot arm"></div>
  <div><h4>MORBI PORTA LIBERO ULLAMCORPER</h4><h5>Morbi porta libero ullamcorper</h5>
  <p>Maple Ridge Country Club, 1840 Birch Ln., Fairview, KY 40299<br>The 22nd annual Golf Tournament and Celebrity Cocktail Party/Auction is a major fundraiser for the many programs offered by the RCL. The golf tournament will be followed as always by a scrumptious dinner, cocktails, and a silent and live auction.<br>If you would like more information please call (555) 406-1187.</p></div>
</article>

<aside>
  <section class="abs widget" style="top:407px;height:233px">
    <div class="widget-head">Featured Auctions</div>
    <div class="feat"><div class="thumb" role="img" aria-label="House"></div><div><span class="feat-title">Auction Tittle Name</span><span class="feat-date">25 July 2014</span><span class="feat-text">Cum sociis natoque penati-bus et magnis dis partur</span></div></div>
    <div class="feat"><div class="thumb" role="img" aria-label="House"></div><div><span class="feat-title">Auction Tittle Name</span><span class="feat-date">25 July 2014</span><span class="feat-text">Cum sociis natoque penati-bus et magnis dis partur</span></div></div>
    <div class="feat"><div class="thumb" role="img" aria-label="House"></div><div><span class="feat-title">Auction Tittle Name</span><span class="feat-date">25 July 2014</span><span class="feat-text">Cum sociis natoque penati-bus et magnis dis partur</span></div></div>
  </section>

  <section class="abs widget" style="top:647px;height:129px">
    <div class="news-title">Newletter Sign Up</div>
    <div class="news-sub">Please Sign up here for latest auctions</div>
    <div class="field">Your Name</div>
    <div class="field">Email address</div>
    <div class="btn">SIGN UP</div>
  </section>

  <section class="abs widget" style="top:786px;height:195px">
    <div class="blog-head">News &amp; Events blog</div>
    <div class="post"><span class="post-title">News Event Tittle here</span><span class="post-text">Etiam est nunc venenatis in tristique eu impe rdiet ac nisl Cum sociis natoque</span></div>
    <div class="post"><span class="post-title">News Event Tittle here</span><span class="post-text">Etiam est nunc venenatis in tristique eu imperdiet ac nisl Cum sociis natoque penati-bus et magnis dis parturient</span></div>
    <div class="post"><span class="post-title">News Event Tittle here</span><span class="post-text">Etiam est nunc venenatis in tristique eu impe rdiet ac nisl Cum sociis natoque</span></div>
  </section>
</aside>

<footer>
  <div class="abs footer"></div>
  <div class="abs footer-contact">
    <h6>Contact Info</h6>
    Linford Auctions, Inc.<br>8800 Fairview Rd., Milltown KY 40299<br>office@linford-example.com<br>Phone: (555) 610-2290
  </div>
  <div class="abs footer-brand"><span class="brand-dot"></span><div class="brand-name">T.R. Kemble<small>Inc. / Auctioneers</small></div></div>
  <div class="abs badges" aria-label="Association memberships">
    <span style="width:58px;height:24px"></span>
    <span style="width:40px;height:30px;border-radius:4px"></span>
    <span style="width:40px;height:40px;border-radius:50%"></span>
  </div>
  <div class="abs copyright">© 2014 Company Name &nbsp;All right reserved &nbsp;Term of Use</div>
</footer>

</body>
</html>
```